Modern Business Card for Larkwell 2018

Our company assumes the best about people. We are creating an online community of entrepreneurs and business leaders who struggle with marketing their business online.

This business card should POP! We recently got a new logo and are launching a new website next month, so our business cards should make a statement that feels:
-Fresh
-Smart
-Trustworthy
-Fun

Target Market(s)

small business owners, entrepreneurs

Industry/Entity Type

Digital Marketing

Contact Information for Business Card

Dimensions: 3.5" x 2"

Font styles to use
Sans Serif

Colors
f37122
ffffff

Requirements
Must have
• We need a business card with a modern, bold design. We will use one side of the card as a lead-generation offer, so text on one side will need to fit up to 140 characters. The business card should stick to our core colors (orange, black, and white).
Nice to have
• We think a vertical "portrait" design could be interesting.
Should not have
• Should not look like a traditional business card. The round icon should stand out from a distance.

```html
<!DOCTYPE html>
<html lang="en">
<head>
<meta charset="utf-8">
<title>Larkwell Business Card</title>
<link href="https://fonts.googleapis.com/css2?family=Roboto:wght@400;700;900&family=Roboto+Condensed:wght@500&display=swap" rel="stylesheet">
<style>
  :root {
    --orange: #f36a28;
    --white: #ffffff;
    --paper: #f2f2f2;
    --ink: #262626;
    --backdrop: #1f1f1f;
    --rule: #1a1a1a;
  }
  * { margin: 0; padding: 0; box-sizing: border-box; }
  html, body { width: 1200px; height: 960px; overflow: hidden; }
  body {
    background: var(--backdrop);
    font-family: "Roboto", Arial, sans-serif;
    position: relative;
  }
  .card {
    position: absolute;
    width: 600px;
    height: 343px;
    text-align: center;
  }
  .card-front { left: 314px; top: 113px; background: var(--paper); color: var(--ink); }
  .card-back { left: 311px; top: 472px; background: var(--orange); color: var(--white); }

  .brand-dot {
    position: absolute;
    left: 289px; top: 34px;
    width: 38px; height: 38px;
    border-radius: 50%;
    background: var(--orange);
  }
  .brand-name {
    position: absolute;
    left: 0; right: 0; top: 82px;
    font-weight: 900;
    font-size: 39px;
    letter-spacing: 1px;
    line-height: 1;
    color: var(--ink);
  }
  .brand-tagline {
    position: absolute;
    left: 0; right: 0; top: 126px;
    font-size: 11px;
    font-weight: 700;
    letter-spacing: 1px;
    color: var(--ink);
  }
  .person-name {
    position: absolute;
    left: 0; right: 0; top: 196px;
    font-family: "Roboto Condensed", Arial, sans-serif;
    font-weight: 500;
    font-size: 24px;
    color: var(--orange);
  }
  .person-title {
    position: absolute;
    left: 0; right: 0; top: 222px;
    font-size: 15px;
    color: var(--ink);
  }
  .contact-rule {
    position: absolute;
    left: 0; right: 0; top: 288px;
    height: 1px;
    background: var(--rule);
  }
  .contact-pill {
    position: absolute;
    left: 85px; top: 271px;
    width: 426px; height: 34px;
    border-radius: 17px;
    background: var(--orange);
    color: var(--white);
    font-size: 14px;
    letter-spacing: 4px;
    line-height: 34px;
  }

  .offer-dot {
    position: absolute;
    left: 271px; top: 22px;
    width: 44px; height: 44px;
    border-radius: 50%;
    background: var(--white);
  }
  .offer-headline {
    position: absolute;
    left: 0; right: 0; top: 76px;
    font-weight: 700;
    font-size: 19px;
    line-height: 21px;
  }
  .offer-text {
    position: absolute;
    left: 0; right: 0; top: 149px;
    font-size: 15px;
    line-height: 18px;
  }
  .offer-url {
    position: absolute;
    left: 0; right: 0; top: 185px;
    font-weight: 700;
    font-size: 19px;
  }
  .notes-box {
    position: absolute;
    left: 20px; top: 224px;
    width: 557px; height: 102px;
    border-radius: 18px;
    background: var(--white);
  }
  .notes-line {
    position: absolute;
    left: 24px; right: 27px;
    height: 1px;
    background: var(--rule);
  }
  .notes-line.first { top: 31px; }
  .notes-line.second { top: 71px; }
</style>
</head>
<body>
  <section class="card card-front" aria-label="Card front">
    <div class="brand-dot"></div>
    <div class="brand-name">LARKWELL</div>
    <div class="brand-tagline">TELL STORIES THAT INSPIRE ACTION</div>
    <div class="person-name">DANA WHITFIELD</div>
    <div class="person-title">STORY MARKETING COACH</div>
    <div class="contact-rule"></div>
    <div class="contact-pill">dana@larkwellnow.com</div>
  </section>

  <section class="card card-back" aria-label="Card back">
    <div class="offer-dot"></div>
    <div class="offer-headline">REACH MORE PEOPLE.<br>MAKE MORE MONEY.<br>CREATE MORE IMPACT.</div>
    <div class="offer-text">Get your free Larkwell, Starter Package and our<br>marketing guide today at</div>
    <div class="offer-url">Larkwellnow.com/start</div>
    <div class="notes-box">
      <div class="notes-line first"></div>
      <div class="notes-line second"></div>
    </div>
  </section>
</body>
</html>
```